Business Card & Email Signature Design || Upmarket + Luxury

Rima Vale Honey, a New Zealand Manuka Honey company needs a Business Card & Email Signature design.

Our logo's are attached in Gold & Black versions, feel free to be creative with how you use the logo and it's patterns in your design.

Style:
- Looking for an Elegant, Luxurious, Upmarket feel.
- Black/Matte Black Card, Gold Foil, UV Embossing

Information to Add:

- Logo
- Company Name: Rima Vale Honey
- Name: Martin Holloway
- Title: Creative Director
- Phone: +64 2815 96 417
- Email: martin@rimavalehoney.example.nz
- Website: www.rimavalehoney.example.nz

- Socials: ***For email Signature Only***
- Facebook: https://www.facebook.com/rimavalehoney/
- Instagram: https://www.instagram.com/rimavalehoney/

Target Market(s)

Asia/Europe Luxury, Upmarket

Contact Information for Business Card

- Logo
- Name: Martin Holloway
- Phone: +64 2815 96 417

Font styles to use
Other font styles liked:
• Champagne & Limousines (Attached)

Requirements
Must have
• Business Card & Email Signature Design.

Looking for a Sleek, Luxury, Upmarket Design.

```html
<!DOCTYPE html>
<html lang="en">
<head>
<meta charset="utf-8">
<title>Rima Vale Honey – Business Card</title>
<link rel="stylesheet" href="https://fonts.googleapis.com/css2?family=Montserrat:wght@400;500&display=swap">
<style>
  :root {
    --backdrop: #1b1b1c;
    --card: #0b0b0b;
    --gold: #d4ae5c;
    --silver: #d9d9d9;
    --muted: #bdbdbd;
  }
  * { box-sizing: border-box; margin: 0; padding: 0; }
  html, body { width: 1200px; height: 1015px; overflow: hidden; }
  body {
    background: var(--backdrop);
    font-family: "Montserrat", sans-serif;
    position: relative;
  }
  .card {
    position: absolute;
    left: 280px;
    width: 640px;
    height: 366px;
    background: var(--card);
    box-shadow: 0 18px 40px rgba(0,0,0,.55);
  }
  .card--front { top: 90px; }
  .card--back { top: 540px; }

  .brand {
    position: absolute;
    display: flex;
    align-items: center;
    gap: 18px;
  }
  .brand__dot {
    width: 46px; height: 46px;
    border-radius: 50%;
    border: 2px solid var(--gold);
  }
  .brand__name {
    color: var(--gold);
    font-weight: 400;
    font-size: 30px;
    letter-spacing: 7px;
    text-transform: uppercase;
    white-space: nowrap;
  }
  .card--front .brand { left: 50%; top: 50%; transform: translate(-50%, -50%); }
  .card--back .brand { left: 78px; top: 70px; }
  .card--back .brand__name { font-size: 26px; letter-spacing: 6px; }

  .contact {
    position: absolute;
    left: 250px;
    top: 168px;
  }
  .contact__name {
    color: var(--gold);
    font-size: 21px;
    font-weight: 500;
    letter-spacing: 1px;
    text-transform: uppercase;
  }
  .contact__title {
    color: var(--silver);
    font-size: 15px;
    margin-top: 2px;
  }
  .contact__list { list-style: none; margin-top: 14px; }
  .contact__item {
    display: flex;
    align-items: center;
    gap: 10px;
    color: var(--silver);
    font-size: 14px;
    line-height: 25px;
  }
  .contact__item--web { color: var(--gold); }
  .contact__icon { width: 16px; height: 16px; flex: none; }
</style>
</head>
<body>
  <section class="card card--front" aria-label="Business card front">
    <div class="brand">
      <span class="brand__dot"></span>
      <span class="brand__name">Rima Vale Honey</span>
    </div>
  </section>

  <section class="card card--back" aria-label="Business card back">
    <div class="brand">
      <span class="brand__dot"></span>
      <span class="brand__name">Rima Vale Honey</span>
    </div>
    <div class="contact">
      <p class="contact__name">Martin Holloway</p>
      <p class="contact__title">Creative Director</p>
      <ul class="contact__list">
        <li class="contact__item">
          <svg class="contact__icon" viewBox="0 0 16 16" fill="none" stroke="#d4ae5c" stroke-width="1.5">
            <path d="M4 1.5 6 5 4.6 6.4a8 8 0 0 0 5 5L11 10l3.5 2-1 2.2C8 14.5 1.5 8 1.8 2.5Z"/>
          </svg>
          +64 2815 96 417
        </li>
        <li class="contact__item">
          <svg class="contact__icon" viewBox="0 0 16 16" fill="none" stroke="#d4ae5c" stroke-width="1.5">
            <rect x="1" y="3.5" width="14" height="9"/><path d="M1 3.5 8 9l7-5.5"/>
          </svg>
          martin@rimavalehoney.example.nz
        </li>
        <li class="contact__item contact__item--web">
          <svg class="contact__icon" viewBox="0 0 16 16" fill="none" stroke="#d4ae5c" stroke-width="1.3">
            <circle cx="8" cy="8" r="6.5"/><ellipse cx="8" cy="8" rx="3" ry="6.5"/><path d="M1.5 8h13M2.5 5h11M2.5 11h11"/>
          </svg>
          www.rimavalehoney.example.nz
        </li>
      </ul>
    </div>
  </section>
</body>
</html>
```